Quillmont Energy b-card redesign

I would like to redesign the card (and power point template) for quillmont energy. We are a developer/owner/operator of high-tech biomass gasification power plants. We take ag waste like nut shells or fruit pits and convert that into electricity in the 1/2 - 3 MW range. I would like to change our company color from red to golden gate bridge orange (C=0,M=69,,Y=100,B=6).

```html
<!DOCTYPE html>
<html lang="en">
<head>
<meta charset="utf-8">
<title>Quillmont Energy – Business Card</title>
<link rel="stylesheet" href="https://fonts.googleapis.com/css2?family=Exo+2:wght@400;500;600&display=swap">
<style>
  :root {
    --bg: #38383a;
    --card: #ffffff;
    --ink: #1f1f20;
    --band: #232324;
    --accent: #ef4a00;
    --rule: #8a8a8a;
    --muted: #9c9c9c;
    --on-dark: #f2f2f2;
  }
  * { margin: 0; padding: 0; box-sizing: border-box; }
  html, body { width: 1200px; height: 817px; overflow: hidden; background: var(--bg); }
  body { font-family: "Exo 2", sans-serif; color: var(--ink); }

  .card {
    position: absolute; left: 100px; top: 123px;
    width: 1000px; height: 570px;
    background: var(--card); border-radius: 40px; overflow: hidden;
  }

  .brand {
    position: absolute; left: 150px; top: 70px;
    display: flex; align-items: center; gap: 22px;
  }
  .brand-dot { width: 26px; height: 26px; border-radius: 50%; background: var(--accent); }
  .brand-name {
    font-size: 56px; font-weight: 500; letter-spacing: 3px;
    color: var(--ink); text-transform: uppercase; line-height: 1;
  }

  .bands { position: absolute; left: 0; top: 0; }

  .holder {
    position: absolute; left: 40px; top: 232px; height: 38px;
    display: flex; align-items: center; gap: 16px; color: var(--on-dark);
  }
  .holder-name { font-size: 30px; font-weight: 500; letter-spacing: 1px; text-transform: uppercase; }
  .holder-sep { font-size: 30px; }
  .holder-title { font-size: 19px; font-weight: 500; letter-spacing: 1px; text-transform: uppercase; }

  .contacts {
    position: absolute; left: 0; top: 300px; width: 1000px;
    display: flex;
  }
  .contact {
    flex: 1; display: flex; flex-direction: column; align-items: center; gap: 26px;
    padding: 0 12px;
  }
  .contact + .contact { border-left: 2px solid var(--rule); }
  .contact-icon {
    width: 78px; height: 78px; border-radius: 50%; background: var(--band);
    display: flex; align-items: center; justify-content: center;
  }
  .contact-text {
    font-size: 25px; font-weight: 500; letter-spacing: 0.5px;
    padding-bottom: 12px; white-space: nowrap;
  }

  .address {
    position: absolute; left: 0; top: 478px; width: 1000px; height: 48px;
    background: var(--band); color: var(--on-dark);
    display: flex; align-items: center; gap: 16px; padding-left: 44px;
    font-size: 22px; letter-spacing: 2px;
  }
</style>
</head>
<body>
  <main class="card">
    <svg class="bands" width="1000" height="300" viewBox="0 0 1000 300" aria-hidden="true">
      <polygon points="0,226 600,226 640,170 1000,170 1000,216 662,216 622,274 0,274" fill="var(--band)"/>
    </svg>

    <div class="brand">
      <span class="brand-dot"></span>
      <span class="brand-name">Quillmont Energy</span>
    </div>

    <div class="holder">
      <svg width="34" height="36" viewBox="0 0 34 36" aria-hidden="true">
        <circle cx="17" cy="10" r="9" fill="var(--muted)"/>
        <path d="M1 36 C1 24 8 20 17 20 C26 20 33 24 33 36 Z" fill="var(--muted)"/>
      </svg>
      <span class="holder-name">Marcus Ellery</span>
      <span class="holder-sep">|</span>
      <span class="holder-title">General Manager</span>
    </div>

    <section class="contacts">
      <div class="contact">
        <span class="contact-icon">
          <svg width="26" height="40" viewBox="0 0 26 40" aria-hidden="true">
            <rect x="2" y="2" width="22" height="36" rx="4" fill="none" stroke="#fff" stroke-width="3"/>
            <line x1="6" y1="30" x2="20" y2="30" stroke="#fff" stroke-width="2"/>
            <circle cx="13" cy="34" r="1.6" fill="#fff"/>
          </svg>
        </span>
        <span class="contact-text">014 275 8830</span>
      </div>
      <div class="contact">
        <span class="contact-icon">
          <svg width="40" height="28" viewBox="0 0 40 28" aria-hidden="true">
            <rect x="2" y="2" width="36" height="24" fill="none" stroke="#fff" stroke-width="3"/>
            <polyline points="2,2 20,16 38,2" fill="none" stroke="#fff" stroke-width="3"/>
          </svg>
        </span>
        <span class="contact-text">marcus@quillmont.com</span>
      </div>
      <div class="contact">
        <span class="contact-icon">
          <svg width="42" height="42" viewBox="0 0 42 42" aria-hidden="true" fill="none" stroke="#fff" stroke-width="2.5">
            <circle cx="21" cy="21" r="18"/>
            <ellipse cx="21" cy="21" rx="8" ry="18"/>
            <line x1="3" y1="21" x2="39" y2="21"/>
            <line x1="6" y1="12" x2="36" y2="12"/>
            <line x1="6" y1="30" x2="36" y2="30"/>
          </svg>
        </span>
        <span class="contact-text">www.quillmont.com</span>
      </div>
    </section>

    <div class="address">
      <svg width="20" height="28" viewBox="0 0 20 28" aria-hidden="true">
        <path d="M10 0 C4.5 0 0 4.5 0 10 C0 17 10 28 10 28 C10 28 20 17 20 10 C20 4.5 15.5 0 10 0 Z" fill="var(--on-dark)"/>
        <circle cx="10" cy="10" r="4" fill="var(--band)"/>
      </svg>
      <span>027,9th floor,Harbor Mill Road QLM</span>
    </div>
  </main>
</body>
</html>
```